Moderne Visitenkarten für Medizintechnikfirma
Zielgruppe
Vertriebsfirma von moderner und innovativer Medizintechnik
Zielgruppe: Ärzte, Kliniken, Medizintechnikfirmen, Patienten
Aufgabenstellung
Besonderes, modernes, auffälliges und ansprechendes Design ohne überladen oder aufdringlich zu sein
Farbenorientierung kann am Logo und der Website geschehen. Wenn zum Logo harmonierend, sind aber auch andere Farben gerne gesehen.
Format: eher horizontal, vertikal aber auch möglich, abgerundete Ecken einplanen
Wenn möglich folgende Infos bitte schon auf die Karten bringen (pro Person eine Karte):
Konrad Faltermann (CEO)
konrad.faltermann@vitalis-partner.de
(Vitalis Partner GmbH
Lindenhof 12
26210 Grünstedt)
www.vitalis-partner.de
info@vitalis-partner.de
Jonas Prasken (CoS)
jonas.prasken@vitalis-partner.de
Die allgemeinen Firmeninfos können deutlich kleiner sein. Anschrift nur wenn es dadurch nicht zu viel werden würde.

```html
<!DOCTYPE html>
<html lang="de">
<head>
<meta charset="utf-8">
<title>Vitalis Partner – Visitenkarten</title>
<link rel="stylesheet" href="https://fonts.googleapis.com/css2?family=Montserrat:wght@400;500;600&display=swap">
<style>
  :root {
    --board: #c8c6c7;
    --paper: #ffffff;
    --brand-purple: #50387a;
    --brand-orange: #e8461b;
    --ink: #1d1d1d;
    --label: #222222;
  }
  html, body { margin: 0; padding: 0; overflow: hidden; }
  body {
    width: 1200px; height: 623px; position: relative;
    background: var(--board);
    font-family: "Montserrat", Arial, sans-serif;
    color: var(--ink);
  }
  .version-label {
    position: absolute; left: 20px;
    font-size: 11px; font-weight: 400; color: var(--label);
  }
  .card {
    position: absolute; width: 216px; height: 140px;
    background: var(--paper); overflow: hidden;
  }
  .card--purple { background: var(--brand-purple); }

  .contact-lines, .company-lines, .web-lines {
    position: absolute; margin: 0; padding: 0; list-style: none;
    font-size: 5.6px; line-height: 9.3px; font-weight: 500; color: var(--ink);
  }
  .contact-lines { left: 13.5px; top: 40.5px; }
  .company-lines { left: 13.5px; top: 105.5px; }
  .web-lines { left: 134px; top: 105.5px; }
  .divider {
    position: absolute; left: 13.5px; top: 86px;
    width: 89px; height: 1px; background: var(--brand-orange);
  }
  .corner-mark {
    position: absolute; right: 14px; top: 44px;
    display: flex; align-items: center; gap: 3px;
    font-size: 7px; font-weight: 600; color: var(--brand-purple);
  }
  .dot { display: inline-block; border-radius: 50%; background: var(--brand-orange); }
  .corner-mark .dot { width: 5px; height: 5px; }

  .wordmark {
    position: absolute; top: 50%; transform: translateY(-50%);
    display: flex; align-items: center; gap: 6px;
    font-size: 15.5px; font-weight: 600; color: var(--brand-purple);
    white-space: nowrap;
  }
  .wordmark .dot { width: 9px; height: 9px; }
  .wordmark--centered { left: 50%; transform: translate(-50%, -50%); }
  .wordmark--offset { left: 40px; font-size: 13px; }
  .wordmark--offset .dot { width: 8px; height: 8px; }
  .card--purple .wordmark { color: var(--paper); }

  .faint-disc {
    position: absolute; right: -40px; bottom: -50px;
    width: 130px; height: 130px; border-radius: 50%;
    background: radial-gradient(circle, rgba(80,56,122,0.12), rgba(80,56,122,0.04));
  }
</style>
</head>
<body>

  <div class="version-label" style="top:64px">v1</div>
  <div class="version-label" style="top:229px">v2</div>
  <div class="version-label" style="top:393px">v3</div>

  <!-- Row v1 -->
  <section class="card card--front" style="left:54px; top:67px">
    <ul class="contact-lines"><li>Konrad Faltermann (CEO)</li><li>+4915298840276</li><li>konrad.faltermann@vitalis-partner.de</li></ul>
    <div class="corner-mark"><span>Vitalis Partner</span><span class="dot"></span></div>
    <div class="divider"></div>
    <ul class="company-lines"><li>Vitalis Partner GmbH</li><li>Lindenhof 12</li><li>26210 Grünstedt</li></ul>
    <ul class="web-lines"><li>www.vitalis-partner.de</li><li>info@vitalis-partner.de</li><li>0800-5518320</li></ul>
  </section>
  <section class="card card--back" style="left:331px; top:67px">
    <div class="wordmark wordmark--centered"><span class="dot"></span><span>Vitalis Partner</span></div>
  </section>
  <section class="card card--front" style="left:653px; top:67px">
    <ul class="contact-lines"><li>Jonas Prasken (CoS)</li><li>+4917634407719</li><li>jonas.prasken@vitalis-partner.de</li></ul>
    <div class="corner-mark"><span>Vitalis Partner</span><span class="dot"></span></div>
    <div class="divider"></div>
    <ul class="company-lines"><li>Vitalis Partner GmbH</li><li>Lindenhof 12</li><li>26210 Grünstedt</li></ul>
    <ul class="web-lines"><li>www.vitalis-partner.de</li><li>info@vitalis-partner.de</li><li>0800-5518320</li></ul>
  </section>
  <section class="card card--back" style="left:930px; top:67px">
    <div class="wordmark wordmark--centered"><span class="dot"></span><span>Vitalis Partner</span></div>
  </section>

  <!-- Row v2 -->
  <section class="card card--front" style="left:54px; top:240px">
    <ul class="contact-lines"><li>Konrad Faltermann (CEO)</li><li>+4915298840276</li><li>konrad.faltermann@vitalis-partner.de</li></ul>
    <div class="corner-mark"><span>Vitalis Partner</span><span class="dot"></span></div>
    <div class="divider"></div>
    <ul class="company-lines"><li>Vitalis Partner GmbH</li><li>Lindenhof 12</li><li>26210 Grünstedt</li></ul>
    <ul class="web-lines"><li>www.vitalis-partner.de</li><li>info@vitalis-partner.de</li><li>0800-5518320</li></ul>
  </section>
  <section class="card card--back card--purple" style="left:331px; top:240px">
    <div class="wordmark wordmark--centered"><span class="dot"></span><span>Vitalis Partner</span></div>
  </section>
  <section class="card card--front" style="left:653px; top:240px">
    <ul class="contact-lines"><li>Jonas Prasken (CoS)</li><li>+4917634407719</li><li>jonas.prasken@vitalis-partner.de</li></ul>
    <div class="corner-mark"><span>Vitalis Partner</span><span class="dot"></span></div>
    <div class="divider"></div>
    <ul class="company-lines"><li>Vitalis Partner GmbH</li><li>Lindenhof 12</li><li>26210 Grünstedt</li></ul>
    <ul class="web-lines"><li>www.vitalis-partner.de</li><li>info@vitalis-partner.de</li><li>0800-5518320</li></ul>
  </section>
  <section class="card card--back card--purple" style="left:930px; top:240px">
    <div class="wordmark wordmark--centered"><span class="dot"></span><span>Vitalis Partner</span></div>
  </section>

  <!-- Row v3 -->
  <section class="card card--front" style="left:54px; top:414px">
    <ul class="contact-lines"><li>Konrad Faltermann (CEO)</li><li>+4915298840276</li><li>konrad.faltermann@vitalis-partner.de</li></ul>
    <div class="corner-mark"><span>Vitalis Partner</span><span class="dot"></span></div>
    <div class="divider"></div>
    <ul class="company-lines"><li>Vitalis Partner GmbH</li><li>Lindenhof 12</li><li>26210 Grünstedt</li></ul>
    <ul class="web-lines"><li>www.vitalis-partner.de</li><li>info@vitalis-partner.de</li><li>0800-5518320</li></ul>
  </section>
  <section class="card card--back" style="left:331px; top:414px">
    <div class="faint-disc"></div>
    <div class="wordmark wordmark--offset"><span class="dot"></span><span>Vitalis Partner</span></div>
  </section>
  <section class="card card--front" style="left:653px; top:414px">
    <ul class="contact-lines"><li>Jonas Prasken (CoS)</li><li>+4917634407719</li><li>jonas.prasken@vitalis-partner.de</li></ul>
    <div class="corner-mark"><span>Vitalis Partner</span><span class="dot"></span></div>
    <div class="divider"></div>
    <ul class="company-lines"><li>Vitalis Partner GmbH</li><li>Lindenhof 12</li><li>26210 Grünstedt</li></ul>
    <ul class="web-lines"><li>www.vitalis-partner.de</li><li>info@vitalis-partner.de</li><li>0800-5518320</li></ul>
  </section>
  <section class="card card--back" style="left:930px; top:414px">
    <div class="faint-disc"></div>
    <div class="wordmark wordmark--offset"><span class="dot"></span><span>Vitalis Partner</span></div>
  </section>

</body>
</html>
```